International online gaming platform needs a game UI design

1. We need a game interface for three kinds of theme based on our guideline and sample mockup.
2. The product type is the online casino games related, we need a series of casino games UIs, however, we can start on the game lobby first.
3. Three theme you might choose from or refer to:
A. 3D look & feel
B. Realistic casino theme
C. Richness and grandeur
D. European casino style
4. NOT ALLOWED to change the design layout.
MUST follow our sample mock up and ONLY redefine the design style.
5. All items must be in a stand-alone component, eg. Button, Tab, Icon,... etc.
6. We need the layout in vector shape, but we can review in JPG or PNG format.
7. The image size: 1366 x 768

Updated:
1. All items and their positions should be same as the sample UI we provided.
Please redesign all the items and create a new theme for it.
No need to create a new layout.
2. Although we accept the draft design, but all the items in UI should be completed.
3. All the wordings in the sample UI are confirmed, you might change the fonts.
4. For the avatar in the left hand side, you don't have to redraw it.
We already have our own avatar system implemented.
5. All the items such as icons, tabs, and buttons are free to redesign.

Dear designers,

We've increased our budget and raise the prize money to 800 USD.  
We also accept the draft design in PNG format and we can go through the details in handover stage.
Thank you very much. 

Reason: Dear designers, We decided to extend the deadline by 7 days. As mentioned in the task description, we are looking for a new style of design and you might refer to the below style. A. 3D look & feel B. Realistic casino theme C. Richness and grandeur D. European casino style If you are still interested in our project, please send us your work. Thank you very much!

```html
<!DOCTYPE html>
<html lang="en">
<head>
<meta charset="utf-8">
<title>Grand Salon – Game Lobby</title>
<link href="https://fonts.googleapis.com/css2?family=Source+Sans+3:wght@400;600;700&family=Cinzel:wght@700&family=Great+Vibes&display=swap" rel="stylesheet">
<style>
:root{
  --gold:#d6ae48;
  --gold-light:#f4dc86;
  --gold-mid:#e6c462;
  --gold-dark:#8f6a1c;
  --maroon:#5c1010;
  --maroon-deep:#3a0808;
  --red:#b22a1c;
  --red-light:#d8452c;
  --brown:#3e2510;
  --brown-deep:#24140a;
  --felt:#1d3a3a;
  --felt-light:#2c5553;
  --cream:#f6ecd2;
  --ink:#3a2608;
  --orange:#c9701f;
  --sky:#1d5f8c;
}
*{box-sizing:border-box;margin:0;padding:0}
html,body{width:1200px;height:675px;overflow:hidden;background:#1a0d05}
body{font-family:"Source Sans 3",sans-serif;color:var(--ink);position:relative}
.abs{position:absolute}
.gold-btn{
  position:absolute;display:flex;align-items:center;justify-content:center;gap:8px;
  background:linear-gradient(180deg,var(--gold-light),var(--gold) 55%,#c39a36);
  border:1px solid var(--gold-dark);border-radius:4px;
  box-shadow:inset 0 1px 0 #fff6c8,0 1px 2px rgba(0,0,0,.45);
  color:var(--ink);font-size:13px;font-weight:600;
}
/* top bar */
.top-bar{left:0;top:0;width:1200px;height:38px;background:linear-gradient(180deg,#7a1a12,var(--maroon) 60%,var(--maroon-deep));border-bottom:2px solid var(--gold)}
.brand{left:0;top:0;height:38px;width:285px;background:linear-gradient(180deg,#9e2a18,#6a140e);clip-path:polygon(0 0,100% 0,88% 100%,0 100%);display:flex;align-items:center;gap:8px;padding-left:10px}
.brand-mark{width:22px;height:22px;border-radius:50%;background:var(--gold-light)}
.brand-name{font-family:"Source Sans 3",sans-serif;font-weight:700;font-size:27px;color:var(--gold-light);letter-spacing:1px}
.tool{top:5px;width:30px;height:27px;padding:0}
.tool svg{width:18px;height:18px}
.tool.close{background:linear-gradient(180deg,var(--red-light),var(--red));border-color:#f1c16a}
/* sidebar */
.sidebar{left:0;top:38px;width:187px;height:600px;background:linear-gradient(90deg,#c79b34,var(--gold-mid) 40%,#c99e38)}
.date-box{left:15px;top:12px;width:157px;height:35px;background:linear-gradient(180deg,#f2d98a,#e0bb59);border:2px solid var(--gold-dark);border-radius:4px;font-size:11.5px;display:flex;align-items:center;justify-content:center}
.avatar{left:20px;top:65px;width:147px;height:140px;border:2px solid var(--gold-dark);background:linear-gradient(180deg,#0d2c44,var(--sky))}
.player-name{left:20px;top:204px;width:147px;height:29px;background:var(--red);border:2px solid var(--gold-dark);color:var(--gold-light);font-size:12.5px;display:flex;align-items:center;padding-left:28px}
.player-name svg{position:absolute;right:6px;top:5px;width:15px;height:15px}
.knob{left:78px;top:243px;width:34px;height:34px;border-radius:50%;background:radial-gradient(circle at 40% 35%,var(--gold-light),var(--gold) 50%,var(--gold-dark));border:2px solid #7a5614}
.side-panel{left:15px;top:267px;width:157px;height:315px;background:radial-gradient(ellipse at 50% 75%,#d98432,var(--orange) 60%,#a9581a);border:2px solid var(--gold-dark);border-radius:3px}
.side-btn{left:28px;width:130px;height:30px;justify-content:flex-start;padding-left:8px;font-size:11.5px;font-weight:400;gap:6px}
.side-btn svg{width:15px;height:15px}
/* main frame */
.main{left:187px;top:38px;width:1013px;height:600px;background:linear-gradient(180deg,#caa142,var(--gold) 30%,#c19537)}
.game-tab{top:6px;height:48px;background:linear-gradient(180deg,#8c1d14,var(--maroon));border:3px solid var(--gold-light);outline:1px solid var(--gold-dark);display:flex;align-items:center;justify-content:center;gap:10px;color:var(--gold-light);font-family:"Great Vibes",cursive;font-size:27px}
.tab-icon{width:40px;height:34px;border-radius:3px;background:linear-gradient(180deg,#e7c36a,#a77a25)}
.featured{left:13px;top:62px;width:287px;height:130px;background:linear-gradient(180deg,var(--gold-light),var(--gold));border:2px solid var(--gold-dark);border-radius:4px}
.dealer-strip{left:300px;top:75px;width:698px;height:107px;background:linear-gradient(180deg,#4a2c12,var(--brown));border:2px solid var(--gold-dark)}
.dealer-card{position:absolute;background:linear-gradient(180deg,var(--gold-light),var(--gold));border:1px solid var(--gold-dark)}
.dealer-photo{position:absolute;border:2px solid var(--gold-dark);background:linear-gradient(180deg,#1a4f78,#0f3553)}
.road{position:absolute;background:#fff;border:1px solid #c9b78a}
.dealer-name{position:absolute;left:0;bottom:0;height:24px;display:flex;align-items:center;padding-left:8px;font-size:11px;background:linear-gradient(180deg,#e3c15e,#cda443)}
.deal-count{position:absolute;right:0;bottom:0;height:24px;background:var(--red);color:var(--gold-light);font-size:11px;display:flex;align-items:center;padding:0 6px}
.filter-bar{left:13px;top:198px;width:985px;height:42px}
.filter-track{left:183px;top:4px;width:285px;height:30px;background:linear-gradient(180deg,#caa03c,#b88d2c);border:1px solid var(--gold-dark);border-radius:3px}
.filter-btn{top:4px;height:30px;font-size:12.5px;font-weight:400}
.filter-btn svg{width:18px;height:18px}
/* table grid */
.table-grid{left:13px;top:247px;width:985px;height:340px;background:linear-gradient(180deg,#4e3115,var(--brown-deep));border:2px solid var(--gold-dark);border-radius:3px}
.table-card{position:absolute;width:306px;height:146px;background:linear-gradient(180deg,var(--gold-light),var(--gold));border:1px solid var(--gold-dark);border-radius:4px}
.table-head{position:absolute;left:2px;top:2px;width:300px;height:40px;background:linear-gradient(180deg,#4b2e12,var(--brown));border-radius:3px}
.table-name{position:absolute;left:6px;top:4px;font-size:10.5px;color:var(--gold-mid);line-height:12px}
.table-name span{display:block;color:var(--cream)}
.table-comm{position:absolute;right:6px;top:4px;text-align:right;font-size:10.5px;color:var(--gold-mid);line-height:12px}
.table-comm span{display:block;color:var(--cream)}
.join{position:absolute;left:115px;top:-6px;width:76px;height:52px;border-radius:50%;background:radial-gradient(ellipse at 50% 40%,var(--gold-light),var(--gold) 60%,#b58a2a);border:2px solid var(--gold-dark);display:flex;align-items:center;justify-content:center;font-family:"Cinzel",serif;font-size:12.5px;color:var(--ink)}
.felt{position:absolute;left:0;top:54px;width:306px;height:55px}
.seats{position:absolute;left:4px;top:113px;display:flex;gap:4px}
.seat{width:39px;height:30px;border:1px solid var(--gold-dark);border-radius:3px;background:linear-gradient(180deg,var(--gold-light),var(--gold));display:flex;align-items:center;justify-content:center}
.seat svg{width:18px;height:18px}
.seat.more{background:linear-gradient(180deg,var(--red-light),var(--red))}
.scroll-track{left:968px;top:10px;width:8px;height:318px;background:#1a0e05;border:1px solid var(--gold-dark);border-radius:4px}
.scroll-thumb{left:964px;top:8px;width:16px;height:16px;border-radius:50%;background:radial-gradient(circle at 40% 35%,var(--gold-light),var(--gold-dark))}
/* footer */
.footer{left:0;top:638px;width:1200px;height:37px;background:linear-gradient(180deg,#d8b050,var(--gold) 60%,#b88c2e)}
.footer-box{top:3px;height:28px;border:1px solid var(--gold-dark);border-radius:3px;display:flex;align-items:center;justify-content:center;font-size:13px}
.balance-label{left:935px;width:73px;background:linear-gradient(180deg,var(--gold-light),var(--gold))}
.currency{left:1010px;width:54px;background:linear-gradient(180deg,var(--gold-light),var(--gold))}
.balance-value{left:1066px;width:124px;background:linear-gradient(180deg,#a3200f,#7c160c);color:var(--cream);font-weight:600;font-size:14px}
</style>
</head>
<body>

<svg width="0" height="0" style="position:absolute" aria-hidden="true">
  <defs>
    <symbol id="felt-layout" viewBox="0 0 306 55">
      <polygon points="30,5 276,5 298,50 8,50" fill="var(--felt)" stroke="#e8e2cf" stroke-width="1.2"/>
      <line x1="19" y1="27" x2="287" y2="27" stroke="#e8e2cf" stroke-width="1"/>
      <g stroke="#e8e2cf" stroke-width="0.9">
        <line x1="65" y1="5" x2="49" y2="50"/><line x1="100" y1="5" x2="91" y2="50"/>
        <line x1="135" y1="5" x2="132" y2="50"/><line x1="171" y1="5" x2="174" y2="50"/>
        <line x1="206" y1="5" x2="215" y2="50"/><line x1="241" y1="5" x2="257" y2="50"/>
      </g>
      <g font-family="Cinzel,serif" font-size="10" fill="var(--gold-mid)" text-anchor="middle">
        <text x="45" y="21">B</text><text x="81" y="21">B</text><text x="117" y="21">B</text><text x="153" y="21">B</text><text x="189" y="21">B</text><text x="225" y="21">B</text><text x="261" y="21">B</text>
      </g>
      <g font-family="Cinzel,serif" font-size="13" fill="#f3efe2" text-anchor="middle">
        <text x="34" y="45">P</text><text x="74" y="45">P</text><text x="113" y="45">P</text><text x="153" y="45">P</text><text x="193" y="45">P</text><text x="232" y="45">P</text><text x="272" y="45">P</text>
      </g>
    </symbol>
    <symbol id="seat-icon" viewBox="0 0 20 20">
      <circle cx="10" cy="6.5" r="4" fill="var(--brown)"/>
      <path d="M2.5 19c0-5 3.4-7.5 7.5-7.5s7.5 2.5 7.5 7.5z" fill="var(--brown)"/>
    </symbol>
    <symbol id="arrow-down" viewBox="0 0 20 20">
      <path d="M8 2h4v9h4l-6 7-6-7h4z" fill="#f3cf4a"/>
    </symbol>
    <pattern id="road-grid" width="11" height="11" patternUnits="userSpaceOnUse">
      <path d="M11 0H0V11" fill="none" stroke="#cfc6b0" stroke-width="1"/>
    </pattern>
    <symbol id="road" viewBox="0 0 165 77">
      <rect width="165" height="77" fill="url(#road-grid)"/>
      <g fill="none" stroke-width="1.6">
        <circle cx="5.5" cy="5.5" r="3.6" stroke="var(--gold)"/><circle cx="16.5" cy="5.5" r="3.6" stroke="var(--red)"/>
        <circle cx="16.5" cy="16.5" r="3.6" stroke="var(--red)"/><circle cx="27.5" cy="5.5" r="3.6" stroke="var(--gold)"/>
        <circle cx="38.5" cy="5.5" r="3.6" stroke="var(--red)"/><circle cx="49.5" cy="5.5" r="3.6" stroke="var(--gold)"/>
        <circle cx="49.5" cy="16.5" r="3.6" stroke="var(--gold)"/><circle cx="115.5" cy="5.5" r="3.6" stroke="var(--gold)"/>
        <circle cx="126.5" cy="5.5" r="3.6" stroke="var(--red)"/><circle cx="126.5" cy="16.5" r="3.6" stroke="var(--red)"/>
        <circle cx="126.5" cy="27.5" r="3.6" stroke="var(--red)"/><circle cx="137.5" cy="5.5" r="3.6" stroke="var(--gold)"/>
        <circle cx="137.5" cy="16.5" r="3.6" stroke="var(--gold)"/><circle cx="137.5" cy="38.5" r="3.6" stroke="var(--red)"/>
        <circle cx="137.5" cy="49.5" r="3.6" stroke="var(--red)"/><circle cx="126.5" cy="60.5" r="3.6" stroke="var(--red)"/>
      </g>
    </symbol>
  </defs>
</svg>

<header class="abs top-bar">
  <div class="abs brand"><span class="brand-mark"></span><span class="brand-name">GRAND SALON</span></div>
  <button class="gold-btn tool" style="left:933px" aria-label="Switch view"><svg viewBox="0 0 20 20"><rect x="2" y="5" width="16" height="11" fill="none" stroke="var(--brown)" stroke-width="2"/><path d="M6 10h8M11 7l3 3-3 3" stroke="var(--brown)" stroke-width="1.8" fill="none"/></svg></button>
  <button class="gold-btn tool" style="left:978px" aria-label="Zoom out"><svg viewBox="0 0 20 20"><circle cx="8" cy="8" r="5.5" fill="none" stroke="var(--brown)" stroke-width="2"/><path d="M12 12l6 6M5 8h6" stroke="var(--brown)" stroke-width="2"/></svg></button>
  <button class="gold-btn tool" style="left:1023px" aria-label="Zoom in"><svg viewBox="0 0 20 20"><circle cx="8" cy="8" r="5.5" fill="none" stroke="var(--brown)" stroke-width="2"/><path d="M12 12l6 6M5 8h6M8 5v6" stroke="var(--brown)" stroke-width="2"/></svg></button>
  <button class="gold-btn tool" style="left:1066px" aria-label="Music"><svg viewBox="0 0 20 20"><path d="M7 15V4l10-2v11" stroke="var(--brown)" stroke-width="2" fill="none"/><circle cx="5" cy="15" r="2.5" fill="var(--brown)"/><circle cx="15" cy="13" r="2.5" fill="var(--brown)"/></svg></button>
  <button class="gold-btn tool" style="left:1109px" aria-label="Full screen"><svg viewBox="0 0 20 20"><path d="M3 7V3h4M13 3h4v4M17 13v4h-4M7 17H3v-4" stroke="var(--brown)" stroke-width="2" fill="none"/><rect x="7" y="7" width="6" height="6" fill="var(--brown)"/></svg></button>
  <button class="gold-btn tool close" style="left:1150px" aria-label="Close"><svg viewBox="0 0 20 20"><circle cx="10" cy="10" r="7" fill="none" stroke="#f7dc8a" stroke-width="2"/><path d="M7 7l6 6M13 7l-6 6" stroke="#f7dc8a" stroke-width="2"/></svg></button>
</header>

<aside class="abs sidebar">
  <div class="abs date-box">1/28/2014 &nbsp;06:54 &nbsp;PM GMT+8</div>
  <div class="abs avatar" role="img" aria-label="Player avatar"></div>
  <div class="abs player-name">ALLos848767
    <svg viewBox="0 0 16 16"><rect x="1.5" y="3" width="11" height="11" fill="none" stroke="var(--gold-light)" stroke-width="1.5"/><path d="M7 9l7-7" stroke="var(--gold-light)" stroke-width="2"/></svg>
  </div>
  <div class="abs side-panel"></div>
  <div class="abs knob"></div>
  <button class="gold-btn side-btn" style="top:297px"><svg viewBox="0 0 16 16"><path d="M2 3h12v8H7l-3 3v-3H2z" fill="var(--brown)"/></svg>Announcements</button>
  <button class="gold-btn side-btn" style="top:336px"><svg viewBox="0 0 16 16"><rect x="4" y="1" width="8" height="14" rx="1.5" fill="none" stroke="var(--brown)" stroke-width="1.6"/><path d="M8 4v5" stroke="var(--brown)" stroke-width="1.6"/><circle cx="8" cy="11.5" r="1" fill="var(--brown)"/></svg>Rules &amp; regulations</button>
  <button class="gold-btn side-btn" style="top:375px"><svg viewBox="0 0 16 16"><rect x="1" y="2" width="14" height="9" fill="none" stroke="var(--brown)" stroke-width="1.6"/><path d="M5 14h6M8 11v3" stroke="var(--brown)" stroke-width="1.6"/><circle cx="7" cy="6.5" r="2" fill="none" stroke="var(--brown)" stroke-width="1.4"/></svg>Quick tour</button>
</aside>

<main class="abs main">
  <nav>
    <div class="abs game-tab" style="left:13px;width:233px"><span class="tab-icon" role="img" aria-label="Playing cards icon"></span>Baccarat</div>
    <div class="abs game-tab" style="left:256px;width:224px"><span class="tab-icon" role="img" aria-label="Chip stack icon"></span>Super Six</div>
    <div class="abs game-tab" style="left:491px;width:225px"><span class="tab-icon" role="img" aria-label="Roulette wheel icon"></span>Roulette</div>
    <div class="abs game-tab" style="left:726px;width:227px"><span class="tab-icon" role="img" aria-label="Dice icon"></span>Sic Bo</div>
  </nav>

  <section class="abs featured">
    <div class="dealer-photo" style="left:7px;top:7px;width:84px;height:70px" role="img" aria-label="Dealer photo"></div>
    <svg class="road" style="left:109px;top:5px;width:165px;height:72px" viewBox="0 0 165 77" preserveAspectRatio="none"><use href="#road"/></svg>
    <div class="dealer-name" style="left:7px;bottom:6px;width:180px;background:linear-gradient(180deg,#e9c965,#d0a744);border-top:1px solid var(--gold-dark)">Dealer:&nbsp;<span style="opacity:.8">Name</span></div>
    <div class="deal-count" style="right:6px;bottom:6px;width:80px;font-size:12px;justify-content:center">Deals 999</div>
  </section>

  <section class="abs dealer-strip">
    <div class="dealer-card" style="left:12px;top:5px;width:220px;height:92px">
      <div class="dealer-photo" style="left:8px;top:6px;width:66px;height:58px" role="img" aria-label="Dealer photo"></div>
      <svg class="road" style="left:82px;top:3px;width:132px;height:60px" viewBox="0 0 165 77" preserveAspectRatio="none"><use href="#road"/></svg>
      <div class="dealer-name" style="width:150px">Dealer:&nbsp;Name</div><div class="deal-count">Deals 999</div>
    </div>
    <div class="dealer-card" style="left:238px;top:5px;width:220px;height:92px">
      <div class="dealer-photo" style="left:8px;top:6px;width:66px;height:58px" role="img" aria-label="Dealer photo"></div>
      <svg class="road" style="left:82px;top:3px;width:132px;height:60px" viewBox="0 0 165 77" preserveAspectRatio="none"><use href="#road"/></svg>
      <div class="dealer-name" style="width:150px">Dealer:&nbsp;Name</div><div class="deal-count">Deals 999</div>
    </div>
    <div class="dealer-card" style="left:464px;top:5px;width:220px;height:92px">
      <div class="dealer-photo" style="left:8px;top:6px;width:66px;height:58px" role="img" aria-label="Dealer photo"></div>
      <svg class="road" style="left:82px;top:3px;width:132px;height:60px" viewBox="0 0 165 77" preserveAspectRatio="none"><use href="#road"/></svg>
      <div class="dealer-name" style="width:150px">Dealer:&nbsp;Name</div><div class="deal-count">Deals 999</div>
    </div>
  </section>

  <div class="abs filter-bar">
    <div class="abs filter-track"></div>
    <button class="gold-btn filter-btn" style="left:10px;width:162px;font-weight:600"><svg viewBox="0 0 20 20" style="position:absolute;left:8px"><use href="#seat-icon"/></svg>Multi-player</button>
    <button class="gold-btn filter-btn" style="left:466px;width:106px"><svg viewBox="0 0 20 20"><circle cx="10" cy="10" r="8" fill="none" stroke="var(--brown)" stroke-width="1.6"/><path d="M6 10l3 3 5-6" stroke="var(--brown)" stroke-width="1.8" fill="none"/></svg>Join any</button>
    <button class="gold-btn filter-btn" style="left:578px;width:40px">A→Z</button>
    <button class="gold-btn filter-btn" style="left:624px;width:40px">$↓</button>
    <button class="gold-btn filter-btn" style="left:670px;width:42px">$↑</button>
    <button class="gold-btn filter-btn" style="left:722px;width:44px"><svg viewBox="0 0 24 20" style="width:24px"><use href="#seat-icon" x="0" width="10" height="12" y="5"/><use href="#seat-icon" x="7" width="10" height="12" y="5"/><use href="#seat-icon" x="14" width="10" height="12" y="5"/></svg></button>
    <button class="gold-btn filter-btn" style="left:770px;width:40px">≫3</button>
    <button class="gold-btn filter-btn" style="left:815px;width:42px">≫3</button>
    <button class="gold-btn filter-btn" style="left:862px;width:106px;font-weight:600"><svg viewBox="0 0 20 20"><path d="M10 1.5l2.6 5.5 6 .7-4.4 4.1 1.2 6-5.4-3-5.4 3 1.2-6L1.4 7.7l6-.7z" fill="var(--brown)"/></svg>All limits</button>
  </div>

  <section class="abs table-grid">
    <article class="table-card" style="left:10px;top:10px">
      <div class="table-head"><p class="table-name">Baccarat A5-3C<span>Bet Limit</span></p><p class="table-comm">Commission 0/7<span>0/100</span></p></div>
      <div class="join">JOIN</div>
      <svg class="felt" viewBox="0 0 306 55"><use href="#felt-layout"/></svg>
      <div class="seats"><span class="seat"><svg><use href="#seat-icon"/></svg></span><span class="seat"><svg><use href="#seat-icon"/></svg></span><span class="seat"><svg><use href="#seat-icon"/></svg></span><span class="seat"><svg><use href="#seat-icon"/></svg></span><span class="seat"><svg><use href="#seat-icon"/></svg></span><span class="seat more"><svg><use href="#arrow-down"/></svg></span><span class="seat more"><svg><use href="#arrow-down"/></svg></span></div>
    </article>
    <article class="table-card" style="left:327px;top:10px">
      <div class="table-head"><p class="table-name">Baccarat A5-3C<span>Bet Limit</span></p><p class="table-comm">Commission 0/7<span>0/100</span></p></div>
      <div class="join">JOIN</div>
      <svg class="felt" viewBox="0 0 306 55"><use href="#felt-layout"/></svg>
      <div class="seats"><span class="seat"><svg><use href="#seat-icon"/></svg></span><span class="seat"><svg><use href="#seat-icon"/></svg></span><span class="seat"><svg><use href="#seat-icon"/></svg></span><span class="seat"><svg><use href="#seat-icon"/></svg></span><span class="seat"><svg><use href="#seat-icon"/></svg></span><span class="seat more"><svg><use href="#arrow-down"/></svg></span><span class="seat more"><svg><use href="#arrow-down"/></svg></span></div>
    </article>
    <article class="table-card" style="left:645px;top:10px">
      <div class="table-head"><p class="table-name">Baccarat A5-3C<span>Bet Limit</span></p><p class="table-comm">Commission 0/7<span>0/100</span></p></div>
      <div class="join">JOIN</div>
      <svg class="felt" viewBox="0 0 306 55"><use href="#felt-layout"/></svg>
      <div class="seats"><span class="seat"><svg><use href="#seat-icon"/></svg></span><span class="seat"><svg><use href="#seat-icon"/></svg></span><span class="seat"><svg><use href="#seat-icon"/></svg></span><span class="seat"><svg><use href="#seat-icon"/></svg></span><span class="seat"><svg><use href="#seat-icon"/></svg></span><span class="seat more"><svg><use href="#arrow-down"/></svg></span><span class="seat more"><svg><use href="#arrow-down"/></svg></span></div>
    </article>
    <article class="table-card" style="left:10px;top:173px">
      <div class="table-head"><p class="table-name">Baccarat A5-3C<span>Bet Limit</span></p><p class="table-comm">Commission 0/7<span>0/100</span></p></div>
      <div class="join">JOIN</div>
      <svg class="felt" viewBox="0 0 306 55"><use href="#felt-layout"/></svg>
      <div class="seats"><span class="seat"><svg><use href="#seat-icon"/></svg></span><span class="seat"><svg><use href="#seat-icon"/></svg></span><span class="seat"><svg><use href="#seat-icon"/></svg></span><span class="seat"><svg><use href="#seat-icon"/></svg></span><span class="seat"><svg><use href="#seat-icon"/></svg></span><span class="seat more"><svg><use href="#arrow-down"/></svg></span><span class="seat more"><svg><use href="#arrow-down"/></svg></span></div>
    </article>
    <article class="table-card" style="left:327px;top:173px">
      <div class="table-head"><p class="table-name">Baccarat A5-3C<span>Bet Limit</span></p><p class="table-comm">Commission 0/7<span>0/100</span></p></div>
      <div class="join">JOIN</div>
      <svg class="felt" viewBox="0 0 306 55"><use href="#felt-layout"/></svg>
      <div class="seats"><span class="seat"><svg><use href="#seat-icon"/></svg></span><span class="seat"><svg><use href="#seat-icon"/></svg></span><span class="seat"><svg><use href="#seat-icon"/></svg></span><span class="seat"><svg><use href="#seat-icon"/></svg></span><span class="seat"><svg><use href="#seat-icon"/></svg></span><span class="seat more"><svg><use href="#arrow-down"/></svg></span><span class="seat more"><svg><use href="#arrow-down"/></svg></span></div>
    </article>
    <article class="table-card" style="left:645px;top:173px">
      <div class="table-head"><p class="table-name">Baccarat A5-3C<span>Bet Limit</span></p><p class="table-comm">Commission 0/7<span>0/100</span></p></div>
      <div class="join">JOIN</div>
      <svg class="felt" viewBox="0 0 306 55"><use href="#felt-layout"/></svg>
      <div class="seats"><span class="seat"><svg><use href="#seat-icon"/></svg></span><span class="seat"><svg><use href="#seat-icon"/></svg></span><span class="seat"><svg><use href="#seat-icon"/></svg></span><span class="seat"><svg><use href="#seat-icon"/></svg></span><span class="seat"><svg><use href="#seat-icon"/></svg></span><span class="seat more"><svg><use href="#arrow-down"/></svg></span><span class="seat more"><svg><use href="#arrow-down"/></svg></span></div>
    </article>
    <div class="abs scroll-track"></div>
    <div class="abs scroll-thumb"></div>
  </section>
</main>

<footer class="abs footer">
  <div class="abs footer-box balance-label">Balance</div>
  <div class="abs footer-box currency">$SGD ›</div>
  <div class="abs footer-box balance-value">999,999.99</div>
</footer>

</body>
</html>
```